Consulting company business cards

We have a base design, but would be willing to update. We have a new logo/"tag" that needs to be added. Current business card design is attached for reference into our "style."

Industry/Entity Type

Business

Contact Information for Business Card

Should contain name and title, office number, mobile number if appropriate, e-mail, website, physical address, and company logo.

Font styles to use
Other font styles liked:
• See current card design on KorvandBCard

Colors
0455a3
85acd3
aaaaaa

Requirements
Must have
• Our colors are navy blue, gray, and a lighter blue
Nice to have
• Design that I can easily drop in new names/titles as we hire employees.

```html
<!DOCTYPE html>
<html lang="en">
<head>
<meta charset="utf-8">
<title>Caspen Business Cards</title>
<link href="https://fonts.googleapis.com/css2?family=Oswald:wght@500;600&family=Open+Sans:ital,wght@0,400;0,600;1,700&display=swap" rel="stylesheet">
<style>
  :root {
    --navy: #0a304d;
    --sky: #7eabcb;
    --ink: #4a4a4a;
    --muted: #8a8a8a;
    --rule: #c9c9c9;
    --paper: #ffffff;
    --backdrop: #2b2b2b;
  }
  * { margin: 0; padding: 0; box-sizing: border-box; }
  html, body { width: 1200px; height: 987px; overflow: hidden; }
  body { background: var(--backdrop); position: relative; font-family: "Open Sans", sans-serif; }

  .card {
    position: absolute;
    left: 293px;
    width: 615px;
    height: 352px;
    border-radius: 18px;
    overflow: hidden;
  }
  .card--front { top: 125px; background: var(--paper); }
  .card--back { top: 510px; background: var(--navy); }

  .brand {
    position: absolute;
    left: 50px;
    top: 124px;
    display: flex;
    align-items: center;
    gap: 12px;
  }
  .brand__name {
    font-family: "Oswald", sans-serif;
    font-weight: 600;
    font-size: 54px;
    line-height: 1;
    letter-spacing: 3px;
    color: var(--navy);
  }
  .brand__dot { width: 38px; height: 38px; border-radius: 50%; background: var(--sky); }
  .brand__tagline {
    position: absolute;
    left: 51px;
    top: 188px;
    font-size: 11px;
    letter-spacing: 1.6px;
    color: var(--muted);
  }

  .divider {
    position: absolute;
    left: 319px;
    top: 68px;
    width: 1px;
    height: 188px;
    background: var(--rule);
  }

  .contact { position: absolute; left: 346px; top: 72px; }
  .contact__name {
    font-family: "Oswald", sans-serif;
    font-weight: 600;
    font-size: 25px;
    line-height: 1.1;
    color: var(--navy);
    text-transform: uppercase;
  }
  .contact__title {
    font-family: "Oswald", sans-serif;
    font-weight: 500;
    font-size: 16px;
    line-height: 1.3;
    color: var(--sky);
    text-transform: uppercase;
    margin-bottom: 10px;
  }
  .contact__address { font-size: 15px; line-height: 21px; color: var(--ink); margin-bottom: 6px; }
  .contact__line {
    display: flex;
    align-items: center;
    gap: 9px;
    font-size: 15px;
    line-height: 24px;
    color: var(--ink);
  }
  .contact__line svg { width: 15px; height: 15px; fill: var(--navy); flex: none; }

  .footer-band { position: absolute; left: 0; bottom: 0; width: 615px; height: 42px; }
  .footer-url {
    position: absolute;
    right: 20px;
    bottom: 8px;
    font-style: italic;
    font-weight: 700;
    font-size: 15px;
    letter-spacing: 3.2px;
    color: var(--paper);
  }

  .back-name {
    position: absolute;
    left: 0; right: 0;
    top: 128px;
    text-align: center;
    font-family: "Oswald", sans-serif;
    font-weight: 600;
    font-size: 74px;
    letter-spacing: 5px;
    color: var(--sky);
  }
  .back-url {
    position: absolute;
    left: 0; right: 0;
    top: 290px;
    text-align: center;
    font-size: 16px;
    letter-spacing: 3.4px;
    color: var(--paper);
  }
</style>
</head>
<body>

<section class="card card--front">
  <div class="brand">
    <span class="brand__name">CASPEN</span>
    <span class="brand__dot"></span>
  </div>
  <div class="brand__tagline">A CLOUD CONSULTING COMPANY</div>

  <div class="divider"></div>

  <div class="contact">
    <div class="contact__name">Renata Korvand</div>
    <div class="contact__title">Office Manager</div>
    <div class="contact__address">1180 N Birchfield Ave<br>Marlow Indiana 46011</div>
    <div class="contact__line">
      <svg viewBox="0 0 16 16" aria-hidden="true"><path d="M3.2 1.2 5.6 1l1.3 3.3-1.6 1.2a8 8 0 0 0 5.2 5.2l1.2-1.6L15 10.4l-.2 2.4c-.1 1.2-1.2 2-2.4 1.9C6.4 14.1 1.9 9.6 1.3 3.6c-.1-1.2.7-2.3 1.9-2.4z"/></svg>
      <span>555.214.0380</span>
    </div>
    <div class="contact__line">
      <svg viewBox="0 0 16 16" aria-hidden="true"><path d="M4 1h7l1 1v4H4zM1 7h14v6h-3v-2H4v2H1zM4 12h8v3H4z"/></svg>
      <span>555.214.0391</span>
    </div>
    <div class="contact__line">
      <svg viewBox="0 0 16 16" aria-hidden="true"><path d="M1 3h14v1.2L8 9 1 4.2zM1 5.8l7 4.8 7-4.8V13H1z"/></svg>
      <span>rkorvand@caspencloud.com</span>
    </div>
  </div>

  <svg class="footer-band" viewBox="0 0 615 42" preserveAspectRatio="none" aria-hidden="true">
    <rect x="0" y="6" width="340" height="14" fill="var(--sky)"/>
    <path d="M0 20 H320 Q338 20 345 12" fill="none" stroke="#ffffff" stroke-width="2"/>
    <path d="M0 21 H330 C345 21 345 0 372 0 H615 V42 H0 Z" fill="var(--navy)"/>
  </svg>
  <div class="footer-url">www.caspencloud.com</div>
</section>

<section class="card card--back">
  <div class="back-name">CASPEN</div>
  <div class="back-url">www.caspencloud.com</div>
</section>

</body>
</html>
```